International aerospace industry business needs a new brochure

We need to make a new Brochure 4 pages A4:
- like the old one (file Vermondix_test_coupons_thermal_spray.pdf)
- with the new text (tekst_na_ulotke_v9.docx)
- with the new design as in email graphic (20201019_FINAL_Test Coupons v2.psd or .png).

Requirements
Must have
• design as in email graphic (20201019_FINAL_Test Coupons v2.psd or .png)
with the new text (tekst_na_ulotke_v9.docx)
Nice to have
• photos with our employees on production floor may be used.

```html
<!DOCTYPE html>
<html lang="en">
<head>
<meta charset="utf-8">
<title>Test Coupons – Brochure Page</title>
<link href="https://fonts.googleapis.com/css2?family=Noto+Sans:wght@400;700&display=swap" rel="stylesheet">
<style>
  :root{
    --brand-blue:#3353a1;
    --frame-blue:#3a56a8;
    --panel-grey:#e5e5e5;
    --ink:#1a1a1a;
    --metal-light:#c9ccd0;
    --metal-mid:#9aa0a7;
    --metal-dark:#7e858d;
    --icon-grey:#8a8d90;
    --wave:#d6e6f5;
  }
  *{margin:0;padding:0;box-sizing:border-box}
  html,body{width:848px;height:1200px;overflow:hidden;background:#fff}
  body{position:relative;font-family:Verdana,"Noto Sans",sans-serif;color:var(--ink)}
  .abs{position:absolute}

  .intro-frame,.brand-frame{position:absolute;left:35px;width:760px;border:1.5px solid var(--frame-blue)}
  .intro-frame{top:59px;height:88px}
  .brand-frame{top:454px;height:88px}
  .panel{position:absolute;left:45px;width:741px;background:var(--panel-grey)}
  .intro-panel{top:67px;height:70px;padding:6px 0 0 18px}
  .brand-panel{top:466px;height:64px;padding:5px 0 0 12px}
  .intro-text{color:var(--brand-blue);font-weight:700;font-size:16.4px;line-height:20.5px;letter-spacing:.2px}
  .brand-text{font-size:13.6px;line-height:17px;letter-spacing:.15px}

  .specimen-set{left:633px;top:33px;width:144px;height:170px;border-radius:6px;
    background:linear-gradient(160deg,#d8dadd,#a3a8ae)}

  .section-title{color:var(--brand-blue);font-weight:700;font-size:26px;line-height:30px}
  .advantages-title{left:125px;top:157px}
  .adv-heading{color:var(--brand-blue);font-weight:700;font-size:14.5px;left:125px}
  .adv-text{font-size:14px;line-height:17px;left:125px;letter-spacing:.1px}
  .icon{position:absolute}

  .experience-title{left:35px;top:553px;line-height:30.5px}

  .wave-band{left:0;top:690px;width:848px;height:290px;
    background:linear-gradient(170deg,transparent 20%,rgba(214,230,245,.55) 50%,transparent 80%)}

  .spec-left{position:absolute;left:33px;width:128px;background:linear-gradient(180deg,var(--metal-light),var(--metal-dark))}
  .spec-right{position:absolute;left:669px;width:140px;background:linear-gradient(180deg,var(--metal-light),var(--metal-dark))}

  .item{position:absolute;font-size:14.5px;line-height:18px;letter-spacing:.1px}
  .item-left{left:175px}
  .item-left::before{content:"• "}
  .item-right{right:189px;text-align:right}
  .item-right::after{content:"  •";white-space:pre}
</style>
</head>
<body>

  <div class="intro-frame"></div>
  <div class="panel intro-panel">
    <p class="intro-text">A test coupon or simply a coupon is a small sample of the material<br>used to obtain data of specific properties after the testing.<br>More often it is called a specimen or just a sample.</p>
  </div>
  <div class="abs specimen-set" role="img" aria-label="Assorted metal test specimens: threaded tensile bar, flat bars and discs"></div>

  <h2 class="abs section-title advantages-title">Our Advantages</h2>

  <svg class="icon" style="left:41px;top:209px" width="48" height="68" viewBox="0 0 48 68" aria-hidden="true">
    <path d="M14 38 L6 58 L14 62 L20 44Z M34 38 L42 58 L34 62 L28 44Z" fill="var(--icon-grey)"/>
    <circle cx="24" cy="24" r="17" fill="none" stroke="var(--brand-blue)" stroke-width="9" stroke-dasharray="5 3.2"/>
    <circle cx="24" cy="24" r="14" fill="var(--brand-blue)"/>
    <circle cx="24" cy="24" r="9" fill="#fff"/>
  </svg>
  <h3 class="abs adv-heading" style="top:203px">Quality Assurance</h3>
  <p class="abs adv-text" style="top:238px">We maintain Quality Management System in accordance with<br>ISO 9001: 2015 and AS 9100D: 2016 by qualified staff of internal auditors.</p>

  <svg class="icon" style="left:35px;top:301px" width="70" height="60" viewBox="0 0 70 60" aria-hidden="true">
    <circle cx="22" cy="38" r="14" fill="none" stroke="var(--brand-blue)" stroke-width="9" stroke-dasharray="5 3"/>
    <circle cx="22" cy="38" r="11" fill="var(--brand-blue)"/><circle cx="22" cy="38" r="6" fill="#fff"/>
    <circle cx="55" cy="28" r="9" fill="none" stroke="var(--icon-grey)" stroke-width="6" stroke-dasharray="3.5 2.4"/>
    <circle cx="55" cy="28" r="4" fill="#fff" stroke="var(--icon-grey)" stroke-width="3"/>
    <circle cx="37" cy="10" r="7" fill="none" stroke="var(--icon-grey)" stroke-width="5" stroke-dasharray="3 2"/>
    <circle cx="37" cy="10" r="3" fill="#fff" stroke="var(--icon-grey)" stroke-width="2.5"/>
  </svg>
  <h3 class="abs adv-heading" style="top:287px">Manufacturing processes</h3>
  <p class="abs adv-text" style="top:323px">Using modern machining, loss and additive methods we ensure optimum<br>price / performance ratio while meeting all requirements of the project.</p>

  <svg class="icon" style="left:37px;top:389px" width="70" height="42" viewBox="0 0 70 42" aria-hidden="true">
    <rect x="25" y="0" width="44" height="23" fill="var(--brand-blue)"/>
    <path d="M1 36 V20 L9 8 H22 V27 H69 L65 34 H1Z" fill="var(--icon-grey)"/>
    <path d="M6 20 L11 12 H18 V20Z" fill="#fff"/>
    <g fill="#fff" stroke="var(--icon-grey)" stroke-width="3"><circle cx="11" cy="35" r="4.5"/><circle cx="38" cy="35" r="4.5"/><circle cx="52" cy="35" r="4.5"/></g>
  </svg>
  <h3 class="abs adv-heading" style="top:371px">In-time Delivery</h3>
  <p class="abs adv-text" style="top:406px">Reliable processing from the design phase to the delivery to Customer<br>through the Just-in-Time method.</p>

  <div class="brand-frame"></div>
  <div class="panel brand-panel">
    <p class="brand-text">spec.pieces is a product line of specimens, samples and coupons machined from difficult-to-machine<br>aerospace grade materials such as nickel &amp; cobalt base superalloys, titanium, and hardened steel.<br>The brand is based on experience and know-how of Vermondix company.</p>
  </div>

  <h2 class="abs section-title experience-title">Our experience includes<br>manufacturing the specimens:</h2>

  <div class="abs wave-band" role="img" aria-label="Soft flowing blue line pattern in the background"></div>

  <div class="spec-left" style="top:644px;height:56px;border-radius:50%" role="img" aria-label="Round disc coating adhesion specimen"></div>
  <div class="spec-left" style="top:724px;height:12px" role="img" aria-label="Flat dog-bone tensile specimen"></div>
  <div class="spec-left" style="top:788px;height:45px" role="img" aria-label="Rectangular hardness test block"></div>
  <div class="spec-left" style="top:872px;height:15px;left:28px;width:138px" role="img" aria-label="Thin plate for microstructure evaluation"></div>
  <div class="spec-left" style="top:932px;height:30px;border-radius:8px" role="img" aria-label="Round fatigue test bar"></div>
  <div class="spec-left" style="top:1003px;height:30px" role="img" aria-label="Lap shear test plate"></div>
  <div class="spec-left" style="top:1075px;height:19px" role="img" aria-label="Bend test strip"></div>
  <div class="spec-left" style="top:1127px;height:43px" role="img" aria-label="Erosion test plate"></div>

  <div class="spec-right" style="left:714px;top:614px;width:76px;height:92px;border-radius:6px" role="img" aria-label="Split cylindrical stress corrosion specimen"></div>
  <div class="spec-right" style="top:724px;height:40px" role="img" aria-label="Thin sheet for Hoffman scratch test"></div>
  <div class="spec-right" style="left:693px;top:790px;width:126px;height:48px;border-radius:50%" role="img" aria-label="Disc for cyclic furnace oxidation test"></div>

  <p class="item item-left" style="top:645px">Adhesion cohesive &amp;<br>&nbsp;bond strength test of coating</p>
  <p class="item item-left" style="top:735px">Tensile test</p>
  <p class="item item-left" style="top:803px">Hardness test</p>
  <p class="item item-left" style="top:871px">Microstructure evaluation</p>
  <p class="item item-left" style="top:940px">Fatigue Test</p>
  <p class="item item-left" style="top:1008px">Lap Shear Test</p>
  <p class="item item-left" style="top:1076px">Bend Test</p>
  <p class="item item-left" style="top:1145px">Erosion Test</p>

  <p class="item item-right" style="top:667px">Stress Corrosion Test</p>
  <p class="item item-right" style="top:736px">Hoffman Scratch Test</p>
  <p class="item item-right" style="top:804px">The Cyclic Furnace Oxidation Test (FCT)</p>
  <p class="item item-right" style="top:872px">Lap Shear Test</p>
  <p class="item item-right" style="top:941px">Bend Test</p>
  <p class="item item-right" style="top:1009px">Erosion Test</p>
  <p class="item item-right" style="top:1077px">Stress Corrosion Test</p>
  <p class="item item-right" style="top:1146px">Hoffman Scratch Test</p>

</body>
</html>
```